eCommerce website for a DIY shop & communal center

We need a website for a business called The Maple Bench. The Maple Bench is both a shop and communal establishment where people with shared interests, especially in DIY (Do It Yourself) and crafting, can gather to shop for & work on projects while sharing ideas, equipment, supplies and knowledge. The shop is both brick & motor and online. The physical communal space provides workstations, equipment, tools and supplies and expertise for DIY lovers to create their projects.

Target Market(s)

Middle & upper class DIY enthusiasts, creative hobbyists, budding artists & small business owners

Industry/Entity Type

DIY, Arts & Crafts

Coding

Coded - Design and coding required

Number of Pages Required

5+ page

Requirements
Must have
• Menus to include 1. home page (with about us, operating hours, contacts, location, meet the team); 2. Bench activities (how to DIY at the Bench, booking, equipment & tools, house rules); 3. Bench events (events in the Bench, offsite events); 4. Resources (FAQs, tutorials, blogs, eBooks) and 5. Online shop
Nice to have
• Branding guidelines eg logo colours (see attachment) to influence design. Tillpost shop. Booking feature for activities & events at the Bench.

```html
<!DOCTYPE html>
<html lang="en">
<head>
<meta charset="utf-8">
<title>The Maple Bench – Online Store</title>
<link href="https://fonts.googleapis.com/css2?family=Roboto:wght@400;500;700;900&display=swap" rel="stylesheet">
<style>
:root{
  --orange:#f47a2a;
  --blue:#3b8fd8;
  --ink:#333;
  --muted:#777;
  --line:#e2e2e2;
  --footer:#1d1d1d;
  --footer-text:#cfcfcf;
  --star:#f5b400;
}
*{box-sizing:border-box;margin:0;padding:0}
html,body{width:739px;height:1200px;overflow:hidden}
body{font-family:'Roboto',Arial,sans-serif;color:var(--ink);background:#fff;position:relative}
.topbar{position:absolute;left:0;top:0;width:739px;height:34px;display:flex;align-items:center;justify-content:space-between;padding:0 39px;font-size:10px;color:var(--ink)}
.topbar .phone{display:flex;align-items:center;gap:5px}
.socials{display:flex;gap:5px}
.socials span{width:16px;height:16px;border:1px solid #999;border-radius:50%;display:block}
.nav{position:absolute;left:0;top:34px;width:739px;height:40px;background:#fff;border-top:1px solid var(--line);display:flex;align-items:center;padding:0 39px;font-size:9px;font-weight:700;letter-spacing:.2px}
.nav a{color:var(--ink);text-decoration:none;margin-right:22px}
.nav .right{margin-left:auto;display:flex}
.nav .right a{margin-right:0;margin-left:22px}
.brand{position:absolute;left:321px;top:4px;width:96px;height:96px;border-radius:50%;background:#fff;display:flex;align-items:center;justify-content:center;text-align:center;font-size:14px;font-weight:900;color:var(--orange);line-height:1.05;z-index:2;box-shadow:0 2px 4px rgba(0,0,0,.12)}
.hero{position:absolute;left:0;top:74px;width:739px;height:216px;background:linear-gradient(120deg,#6e5844 0%,#a58c6f 40%,#c9b79c 65%,#5d4a3a 100%)}
.hero::after{content:"";position:absolute;inset:0;background:rgba(0,0,0,.25)}
.hero h1{position:absolute;left:64px;top:105px;z-index:1;color:#fff;font-size:32px;font-weight:700;letter-spacing:.5px}
.sidebar{position:absolute;left:39px;top:305px;width:128px;border:1px solid var(--line);font-size:7.5px}
.sidebar .head{background:var(--blue);color:#fff;font-weight:700;font-size:9px;padding:6px 8px}
.cat{display:flex;justify-content:space-between;font-weight:700;padding:9px 8px;border-top:1px solid var(--line)}
.cat:first-of-type{border-top:none}
.subs{padding:2px 8px 8px 8px}
.subs div{display:flex;align-items:center;gap:4px;color:var(--muted);padding:4px 0}
.subs div::before{content:"";width:6px;height:6px;border:1px solid #aaa;display:block}
.subs .on{color:var(--orange)}
.grid{position:absolute;left:177px;top:305px;width:532px;display:grid;grid-template-columns:repeat(4,1fr);column-gap:9px;row-gap:16px}
.card{text-align:center;font-size:8px}
.card .photo{height:128px;display:block}
.stars{color:var(--star);font-size:8px;letter-spacing:1px;margin-top:6px}
.card .title{font-weight:500;margin-top:3px}
.card .price{color:var(--muted);margin-top:2px}
.pager{position:absolute;left:318px;top:900px;display:flex;gap:4px;font-size:8px}
.pager span{height:18px;min-width:18px;border:1px solid var(--line);display:flex;align-items:center;justify-content:center;padding:0 4px;color:var(--muted)}
.pager .on{background:var(--orange);border-color:var(--orange);color:#fff}
.footer{position:absolute;left:0;top:980px;width:739px;height:220px;background:var(--footer);color:var(--footer-text)}
.fcol{position:absolute;top:50px;font-size:8px;line-height:15px}
.fcol h4{color:#fff;font-size:10px;font-weight:700;margin-bottom:6px;letter-spacing:.3px}
.email{width:150px;height:22px;background:#fff;color:#999;font-size:8px;display:flex;align-items:center;padding-left:8px;margin-top:2px}
.subscribe{width:150px;height:22px;background:var(--orange);color:#fff;font-size:8px;font-weight:700;display:flex;align-items:center;justify-content:center;margin-top:6px;border-radius:11px}
.fsocial{display:flex;gap:7px;justify-content:center;width:150px;margin-top:10px}
.fsocial span{width:18px;height:18px;border-radius:50%;background:#fff;display:block}
.copy{position:absolute;left:0;bottom:0;width:739px;height:32px;border-top:1px solid #333;font-size:7px;text-align:center;line-height:32px;color:#999}
</style>
</head>
<body>
<div class="topbar">
  <div class="phone">
    <svg width="10" height="10" viewBox="0 0 24 24"><path d="M6.6 10.8a15 15 0 0 0 6.6 6.6l2.2-2.2c.3-.3.7-.4 1-.2 1.1.4 2.3.6 3.6.6.6 0 1 .4 1 1V20c0 .6-.4 1-1 1A17 17 0 0 1 3 4c0-.6.4-1 1-1h3.5c.6 0 1 .4 1 1 0 1.3.2 2.5.6 3.6.1.3 0 .7-.2 1z" fill="#333"/></svg>
    555 - 014 - 2290
  </div>
  <div class="socials"><span></span><span></span><span></span></div>
</div>
<nav class="nav">
  <a>HOME</a><a>BENCH ACTIVITIES</a><a>BENCH EVENTS</a>
  <div class="right"><a>RESOURCES</a><a>ONLINE SHOP</a><a>CONTACT US</a></div>
</nav>
<div class="brand">The<br>Maple<br>Bench</div>
<header class="hero" role="img" aria-label="Workshop photo with a mitre saw on a wooden workbench">
  <h1>ONLINE STORE</h1>
</header>

<aside class="sidebar">
  <div class="head">Categories</div>
  <div class="cat"><span>WOODCRAFT</span><span>–</span></div>
  <div class="subs">
    <div class="on">All</div>
    <div>Woodworking (10)</div><div>Pyrography (10)</div><div>Wood turning (10)</div><div>Wood carving (10)</div>
    <div>Glass Blocks (10)</div><div>The essentials (10)</div><div>Pinbox Bonanza (10)</div><div>Pound (10)</div>
  </div>
  <div class="cat"><span>PAMPER ZONE HOBBIES</span><span>+</span></div>
  <div class="cat"><span>FUNCTIONAL ART</span><span>+</span></div>
  <div class="cat"><span>THREADS AND TEXTILE CRAFTS</span><span>+</span></div>
  <div class="cat"><span>PAPERCRAFT</span><span>+</span></div>
  <div class="cat"><span>PAINTING AND OTHER CREATIVE ARTS</span><span>+</span></div>
  <div class="cat"><span>FOOD &amp; DINING HOBBIES</span><span>+</span></div>
  <div class="cat"><span>HOME IMPROVEMENT</span><span>+</span></div>
  <div class="cat"><span>MAKER CULTURE</span><span>+</span></div>
</aside>

<main class="grid">
  <div class="card"><div class="photo" role="img" aria-label="Wooden kitchen cabinet project" style="background:linear-gradient(160deg,#8a7a66,#cfc2ad)"></div><div class="stars">★★★★★</div><div class="title">Lorem Ipsum passage</div><div class="price">From $40.00</div></div>
  <div class="card"><div class="photo" role="img" aria-label="Painted canvas artwork on an easel" style="background:linear-gradient(160deg,#3d6fa8,#d9c24a,#5a8f4a)"></div><div class="stars">★★★★★</div><div class="title">Lorem Ipsum passage</div><div class="price">From $40.00</div></div>
  <div class="card"><div class="photo" role="img" aria-label="Maker holding a finished crafted board" style="background:linear-gradient(160deg,#4e6a3a,#8a9a5a,#2f3a2a)"></div><div class="stars">★★★★★</div><div class="title">Lorem Ipsum passage</div><div class="price">From $40.00</div></div>
  <div class="card"><div class="photo" role="img" aria-label="Wooden dartboard cabinet" style="background:linear-gradient(160deg,#6b2f2a,#b9836a)"></div><div class="stars">★★★★★</div><div class="title">Lorem Ipsum passage</div><div class="price">From $40.00</div></div>
  <div class="card"><div class="photo" role="img" aria-label="Glass block lamp with warm lights" style="background:linear-gradient(160deg,#5a3416,#d98a2a,#7a4a1e)"></div><div class="stars">★★★★★</div><div class="title">Lorem Ipsum passage</div><div class="price">From $40.00</div></div>
  <div class="card"><div class="photo" role="img" aria-label="Stack of wooden pallet boards" style="background:linear-gradient(160deg,#9c8a72,#d8cdb8)"></div><div class="stars">★★★★★</div><div class="title">Lorem Ipsum passage</div><div class="price">From $40.00</div></div>
  <div class="card"><div class="photo" role="img" aria-label="Vertical wooden planter with greenery" style="background:linear-gradient(160deg,#3e5a32,#7b6a52,#a89878)"></div><div class="stars">★★★★★</div><div class="title">Lorem Ipsum passage</div><div class="price">From $40.00</div></div>
  <div class="card"><div class="photo" role="img" aria-label="Framed jersey display case" style="background:linear-gradient(160deg,#b8b0a6,#3a3a3a,#c9c2b8)"></div><div class="stars">★★★★★</div><div class="title">Lorem Ipsum passage</div><div class="price">From $40.00</div></div>
  <div class="card"><div class="photo" role="img" aria-label="Wooden chicken coop in a garden" style="background:linear-gradient(160deg,#8c6a48,#c4a47c,#5e6a3a)"></div><div class="stars">★★★★★</div><div class="title">Lorem Ipsum passage</div><div class="price">From $40.00</div></div>
  <div class="card"><div class="photo" role="img" aria-label="White children's play kitchen" style="background:linear-gradient(160deg,#d8d4ce,#a8a098)"></div><div class="stars">★★★★★</div><div class="title">Lorem Ipsum passage</div><div class="price">From $40.00</div></div>
  <div class="card"><div class="photo" role="img" aria-label="Rustic wooden bench and table set" style="background:linear-gradient(160deg,#6a5640,#b49a78)"></div><div class="stars">★★★★★</div><div class="title">Lorem Ipsum passage</div><div class="price">From $40.00</div></div>
  <div class="card"><div class="photo" role="img" aria-label="Outdoor wooden garden structure" style="background:linear-gradient(160deg,#7a8a5a,#c2a880,#5a4a36)"></div><div class="stars">★★★★★</div><div class="title">Lorem Ipsum passage</div><div class="price">From $40.00</div></div>
</main>

<div class="pager"><span class="on">1</span><span>2</span><span>3</span><span>Next</span></div>

<footer class="footer">
  <div class="fcol" style="left:62px"><h4>ABOUT</h4>Our Story<br>Press<br>Locations<br>Blog<br>Contact Us</div>
  <div class="fcol" style="left:146px"><h4>OUR OFFERING</h4>Projects<br>Sawdust Lounge<br>Parties<br>Classes</div>
  <div class="fcol" style="left:262px"><h4>OTHER</h4>Franchise<br>Gift Cards<br>FAQ<br>Refund Policy</div>
  <div class="fcol" style="left:352px"><h4>CONTACT US</h4>48 Alder Row, Fernvale<br>20417<br>555 - 014 - 2290<br>hello@maplebench.shop</div>
  <div class="fcol" style="left:518px"><h4>GET UPDATES &amp; PROMOS</h4>
    <div class="email">Email Address</div>
    <div class="subscribe">SUBSCRIBE</div>
    <div class="fsocial"><span></span><span></span><span></span><span></span></div>
  </div>
  <div class="copy">Copyright © 2017 The Maple Bench. All rights reserved.</div>
</footer>
</body>
</html>
```